Resposive web site in 4 languages + image gallery + logo design

We need a web page, which will work on all devices.
I have uploaded web page concept.
Company name: Praxelun
Industry/Entity Type
It Company
Logo Text
quality matters
Coding
Coded - Design and coding required
Number of Pages Required
1 page

```html
<!DOCTYPE html>
<html lang="en">
<head>
<meta charset="utf-8">
<title>Praxelun — Woodworks, Stoneworks, Restoration</title>
<link href="https://fonts.googleapis.com/css2?family=Open+Sans:wght@400;600;700;800&display=swap" rel="stylesheet">
<style>
:root{
  --blue:#0b6fc2;
  --blue-dark:#0a5ea6;
  --ink:#1e1e1e;
  --text:#5a5a5a;
  --muted:#8c8c8c;
  --line:#e1e1e1;
  --soft:#f3f3f3;
  --red:#c8242a;
  --footer:#121212;
  --wood-1:#d9c3a0;
  --wood-2:#b89468;
}
*{box-sizing:border-box;margin:0;padding:0}
html,body{width:1200px;height:2853px;overflow:hidden}
body{font-family:"Open Sans",Arial,sans-serif;color:var(--text);background:#fff;position:relative}
.abs{position:absolute}
/* header */
.site-header{top:0;left:0;width:1200px;height:99px;background:#fff;border-bottom:1px solid var(--line)}
.brand{left:99px;top:32px;font-size:27px;font-weight:800;color:var(--ink);letter-spacing:.5px}
.nav{left:377px;top:0;display:flex;height:99px}
.nav a{display:flex;align-items:center;justify-content:center;height:99px;padding:0 18px;font-size:12px;font-weight:600;color:var(--ink);text-decoration:none;text-transform:uppercase}
.nav a.active{background:var(--blue);color:#fff;width:76px;padding:0}
.lang{left:738px;top:32px;width:126px;height:35px;border:1px solid var(--line);display:flex;align-items:center;font-size:10px;color:var(--muted);padding-left:8px;gap:7px}
.lang .dot{width:18px;height:18px;border-radius:50%;background:#c0343f}
.lang .caret{margin-left:auto;width:22px;height:33px;border-left:1px solid var(--line);display:flex;align-items:center;justify-content:center}
.follow{left:884px;top:42px;font-size:12px;color:var(--muted)}
.social-btn{left:941px;top:32px;width:160px;height:36px;background:#3b5a9a;color:#fff;font-size:11.5px;font-weight:600;display:flex;align-items:center;justify-content:center;gap:7px}
.social-btn .sq{width:12px;height:12px;background:#fff}
/* hero */
.hero{top:99px;left:0;width:1200px;height:510px;background:radial-gradient(ellipse at 50% 50%,#e6d3b3 0%,var(--wood-1) 45%,var(--wood-2) 100%)}
.hero-title{top:306px;left:0;width:1200px;text-align:center;font-size:44px;font-weight:800;color:#111;letter-spacing:1px}
.hero-sub{top:370px;left:0;width:1200px;text-align:center;font-size:21px;font-weight:700;color:var(--blue)}
.dots{top:427px;left:566px;display:flex;gap:12px}
.dots span{width:14px;height:14px;border-radius:50%;border:2px solid #fff}
.dots span.on{background:var(--blue)}
/* estimate band */
.estimate{top:609px;left:0;width:1200px;height:87px;background:var(--blue)}
.estimate p{position:absolute;left:99px;top:22px;width:580px;font-size:11px;line-height:20px;color:#e4efff}
.estimate strong{color:#fff;font-size:13px;font-weight:700}
.estimate .field{position:absolute;left:673px;top:26px;width:301px;height:35px;background:#fff;font-size:10px;color:var(--muted);padding:11px 14px}
.estimate .cta{position:absolute;left:980px;top:26px;width:121px;height:35px;background:var(--red);color:#fff;font-size:12px;font-weight:700;display:flex;align-items:center;justify-content:center}
/* section heads */
.section-title{left:99px;font-size:24px;font-weight:700;color:var(--ink)}
.section-lead{left:99px;width:900px;font-size:13px;line-height:26px;color:var(--muted)}
/* service cards */
.service{left:99px;width:1002px;height:299px;border:1px solid var(--line);background:#fff}
.service .photo{position:absolute;left:15px;top:14px;width:306px;height:203px}
.service h3{position:absolute;left:362px;top:22px;font-size:14px;font-weight:700;color:var(--blue)}
.service .copy{position:absolute;left:362px;top:54px;width:610px;font-size:11.5px;line-height:22px;color:var(--text)}
.service .copy p+p{margin-top:10px}
.service .more{display:block;margin-top:14px;font-size:10.5px;font-style:italic;color:var(--blue);text-decoration:underline}
.tags{position:absolute;left:0;bottom:0;width:1000px;height:49px;border-top:1px solid var(--line);display:flex;justify-content:space-around;align-items:center;font-size:10.5px;font-weight:600;color:#444;text-transform:uppercase}
.tags span{display:flex;align-items:center;gap:8px}
.tags svg{width:12px;height:8px}
.ph-wood{background:linear-gradient(135deg,#6b4a2e,#b58a5d 55%,#3d2a1a)}
.ph-stone{background:linear-gradient(135deg,#9aa3ab,#d9dde0 50%,#6e7780)}
.ph-rest{background:linear-gradient(135deg,#2e4d7a,#8aa3c4 55%,#c7a36a)}
.ph-about{background:linear-gradient(135deg,#cfc5b8,#8d7a66 55%,#e8e2d9)}
/* about */
.about{top:1832px;left:0;width:1200px;height:441px;background:var(--soft);border-bottom:1px solid var(--line)}
.about-photo{left:101px;top:1991px;width:386px;height:227px;border:3px solid #fff}
.about-copy{left:534px;top:1992px;width:570px;font-size:11.5px;line-height:25px;color:var(--text)}
.about-copy p+p{margin-top:12px}
.btn{background:linear-gradient(#2f8ad6,var(--blue-dark));color:#fff;font-size:12px;font-weight:700;display:flex;align-items:center;justify-content:center;text-transform:uppercase}
/* contact */
.form-label{left:99px;top:2428px;font-size:11.5px;font-weight:600;color:var(--blue);text-transform:uppercase}
.input{height:42px;border:1px solid var(--line);background:#f7f7f7;font-size:11.5px;color:#777;padding:13px 14px;display:flex;justify-content:space-between}
.input svg{width:13px;height:13px}
.contact-lead{left:732px;top:2426px;width:370px;font-size:10.5px;line-height:20px;color:#666;text-transform:uppercase}
.info-label{left:732px;font-size:12px;font-weight:700;color:var(--blue);text-transform:uppercase}
.info-line{left:732px;display:flex;align-items:center;gap:18px;font-size:12.5px;font-weight:600;color:#333}
.info-line svg{width:20px;height:20px}
.info-line .big{font-size:17px;font-weight:600}
/* footer */
.site-footer{top:2796px;left:0;width:1200px;height:57px;background:var(--footer);color:#ddd;font-size:12px}
.site-footer .copy{position:absolute;left:99px;top:20px}
.site-footer .follow-f{position:absolute;left:870px;top:20px}
.site-footer .circles{position:absolute;left:970px;top:14px;display:flex;gap:8px}
.site-footer .circles span{width:28px;height:28px;border-radius:50%;border:2px solid #ddd}
</style>
</head>
<body>

<header class="site-header abs">
  <div class="brand abs">PRAXELUN</div>
  <nav class="nav abs">
    <a class="active">Home</a><a>Services</a><a>About us</a><a>Contact</a>
  </nav>
  <div class="lang abs"><span class="dot"></span>LANGUAGE<span class="caret"><svg width="8" height="5" viewBox="0 0 8 5"><path d="M0 0h8L4 5z" fill="#999"/></svg></span></div>
  <div class="follow abs">Follow Us:</div>
  <div class="social-btn abs"><span class="sq"></span>Like Us On Friendspace</div>
</header>

<section class="hero abs" role="img" aria-label="Wood shavings and a circular saw blade on a timber board"></section>
<div class="hero-title abs">PRAXELUN</div>
<div class="hero-sub abs">ACCUSANTIUM DOLOREMQUE LAUDANTIUM</div>
<div class="dots abs"><span class="on"></span><span></span><span></span></div>

<section class="estimate abs">
  <p><strong>ARE YOU INTERESTED IN AN ESTIMATE? :</strong> Sed ut perspiciatis unde omnis iste natus error sit tatem accusantium doloremque laudantium, totam rem aperiam, eaque ipsa quae ab illo inventore...</p>
  <div class="field">ENTER YOUR E-MAIL ADDRESS</div>
  <div class="cta">GET A QUOTE</div>
</section>

<h2 class="section-title abs" style="top:727px">OUR SERVICES</h2>
<p class="section-lead abs" style="top:758px">Sed ut perspiciatis unde omnis iste natus error sit voluptatem accusantium doloremque laudantium, totam rem aperiam, eaque ipsa quae ab illo inventore veritatis et quasi architecto beatae vitae dicta sunt explicabo...</p>

<article class="service abs" style="top:837px">
  <div class="photo ph-wood" role="img" aria-label="Craftsman planing a wooden board with a hand plane"></div>
  <h3>WOODWORKS</h3>
  <div class="copy">
    <p>Timber is, in essence, a natural and warm material. Wood is also relatively durable and easy to work with, which has made it a favourite of builders throughout history. Our goal is to offer GALLERY (sliders) suitable products and quality furniture with installation and after-When clicked opens sales</p>
    <p>Service to all of our clients. In order to achieve this, we're this category gallery ready to help our clients in all stages of construction from design to production and maintenance.</p>
    <a class="more">Click Read more information</a>
  </div>
  <div class="tags">
    <span><svg viewBox="0 0 12 8"><path d="M0 4h10M7 1l3 3-3 3" stroke="#0b6fc2" stroke-width="1.6" fill="none"/></svg>Furniture</span>
    <span><svg viewBox="0 0 12 8"><path d="M0 4h10M7 1l3 3-3 3" stroke="#0b6fc2" stroke-width="1.6" fill="none"/></svg>Windows</span>
    <span><svg viewBox="0 0 12 8"><path d="M0 4h10M7 1l3 3-3 3" stroke="#0b6fc2" stroke-width="1.6" fill="none"/></svg>Doors</span>
    <span><svg viewBox="0 0 12 8"><path d="M0 4h10M7 1l3 3-3 3" stroke="#0b6fc2" stroke-width="1.6" fill="none"/></svg>Staircases</span>
    <span><svg viewBox="0 0 12 8"><path d="M0 4h10M7 1l3 3-3 3" stroke="#0b6fc2" stroke-width="1.6" fill="none"/></svg>Woodcarving</span>
    <span><svg viewBox="0 0 12 8"><path d="M0 4h10M7 1l3 3-3 3" stroke="#0b6fc2" stroke-width="1.6" fill="none"/></svg>Graining</span>
  </div>
</article>

<article class="service abs" style="top:1162px">
  <div class="photo ph-stone" role="img" aria-label="Gloved hands laying paving stones with a rubber mallet"></div>
  <h3>STONEWORKS</h3>
  <div class="copy">
    <p>The natural stone found in the ground has been used in construction for centuries because of its durability.<br>A structureGALLERY (sliders) built by a skilled craftsman from natural stone is unique, genuine When clicked opens and durable, and perfect for our bracing climate.</p>
    <p>Our experienced craftsmen are ready to help you in all stages of construction from planning to completion.</p>
    <a class="more" style="margin-top:22px">Click Read more information</a>
  </div>
  <div class="tags">
    <span><svg viewBox="0 0 12 8"><path d="M0 4h10M7 1l3 3-3 3" stroke="#0b6fc2" stroke-width="1.6" fill="none"/></svg>Walls</span>
    <span><svg viewBox="0 0 12 8"><path d="M0 4h10M7 1l3 3-3 3" stroke="#0b6fc2" stroke-width="1.6" fill="none"/></svg>Terraces</span>
    <span><svg viewBox="0 0 12 8"><path d="M0 4h10M7 1l3 3-3 3" stroke="#0b6fc2" stroke-width="1.6" fill="none"/></svg>Paths</span>
    <span><svg viewBox="0 0 12 8"><path d="M0 4h10M7 1l3 3-3 3" stroke="#0b6fc2" stroke-width="1.6" fill="none"/></svg>Outdoor kitchens</span>
    <span><svg viewBox="0 0 12 8"><path d="M0 4h10M7 1l3 3-3 3" stroke="#0b6fc2" stroke-width="1.6" fill="none"/></svg>Fireplaces</span>
    <span><svg viewBox="0 0 12 8"><path d="M0 4h10M7 1l3 3-3 3" stroke="#0b6fc2" stroke-width="1.6" fill="none"/></svg>Smokeries</span>
    <span><svg viewBox="0 0 12 8"><path d="M0 4h10M7 1l3 3-3 3" stroke="#0b6fc2" stroke-width="1.6" fill="none"/></svg>Fences</span>
  </div>
</article>

<article class="service abs" style="top:1487px">
  <div class="photo ph-rest" role="img" aria-label="Workers in ear protection operating a woodworking machine"></div>
  <h3>RESTORATION</h3>
  <div class="copy">
    <p>It's good to see that fixing old things has become popular again in recent years and people are trying to find ways to preserve GALLERY (sliders) valuable old windows and pieces of furniture before deciding to When cliked opens replace them.It is possible to give a new life to almost any</p>
    <p>wooden door,window, piece of furniture or staircase. The extensive experience of our craftsmen will help you achieve the desired result.</p>
    <a class="more">Click Read more information</a>
  </div>
  <div class="tags">
    <span><svg viewBox="0 0 12 8"><path d="M0 4h10M7 1l3 3-3 3" stroke="#0b6fc2" stroke-width="1.6" fill="none"/></svg>Furniture</span>
    <span><svg viewBox="0 0 12 8"><path d="M0 4h10M7 1l3 3-3 3" stroke="#0b6fc2" stroke-width="1.6" fill="none"/></svg>Windows</span>
    <span><svg viewBox="0 0 12 8"><path d="M0 4h10M7 1l3 3-3 3" stroke="#0b6fc2" stroke-width="1.6" fill="none"/></svg>Doors</span>
    <span><svg viewBox="0 0 12 8"><path d="M0 4h10M7 1l3 3-3 3" stroke="#0b6fc2" stroke-width="1.6" fill="none"/></svg>Staircases</span>
    <span><svg viewBox="0 0 12 8"><path d="M0 4h10M7 1l3 3-3 3" stroke="#0b6fc2" stroke-width="1.6" fill="none"/></svg>Floors</span>
    <span><svg viewBox="0 0 12 8"><path d="M0 4h10M7 1l3 3-3 3" stroke="#0b6fc2" stroke-width="1.6" fill="none"/></svg>Special projects</span>
  </div>
</article>

<section class="about abs"></section>
<h2 class="section-title abs" style="top:1880px">ABOUT US</h2>
<p class="section-lead abs" style="top:1911px">Sed ut perspiciatis unde omnis iste natus error sit voluptatem accusantium doloremque laudantium, totam rem aperiam, eaque ipsa quae ab illo inventore veritatis et quasi architecto beatae vitae dicta sunt explicabo...</p>
<div class="about-photo ph-about abs" role="img" aria-label="Carpenter in safety glasses and ear defenders cutting wood"></div>
<div class="about-copy abs">
  <p>Praxelun is a company whose business operations include making wooden products, restoration and building structures from natural stone.LOGO OR IMAGE All of our products are made by craftsmen and specialists who have extensive experience and knowledge in their fields.</p>
  <p>The products we offer are always handmade and we take the requests and ideas of the specific client into account We always strive to achieve the best possible quality.Quality matters, Praxelun</p>
</div>
<div class="btn abs" style="left:533px;top:2166px;width:108px;height:42px">Read more</div>

<h2 class="section-title abs" style="top:2318px">CONTACT</h2>
<p class="section-lead abs" style="top:2349px">Sed ut perspiciatis unde omnis iste natus error sit voluptatem accusantium doloremque laudantium, totam rem aperiam, eaque ipsa quae ab illo inventore veritatis et quasi architecto beatae vitae dicta sunt explicabo...</p>

<div class="form-label abs">Please fill in the following fields if you would like a price quote</div>
<div class="input abs" style="left:99px;top:2465px;width:270px">Your name...<svg viewBox="0 0 13 13"><circle cx="6.5" cy="4" r="3" fill="#bbb"/><path d="M1 13a5.5 5 0 0 1 11 0z" fill="#bbb"/></svg></div>
<div class="input abs" style="left:382px;top:2465px;width:268px">Company...<svg viewBox="0 0 13 13"><rect x="1" y="1" width="11" height="12" fill="#bbb"/><path d="M3 3h2M8 3h2M3 6h2M8 6h2M3 9h2M8 9h2" stroke="#f7f7f7"/></svg></div>
<div class="input abs" style="left:99px;top:2522px;width:270px">Contact email...<svg viewBox="0 0 13 13"><rect x="0.5" y="2.5" width="12" height="8" fill="none" stroke="#bbb"/><path d="M.5 2.5l6 5 6-5" fill="none" stroke="#bbb"/></svg></div>
<div class="input abs" style="left:382px;top:2522px;width:268px">Contact phone...<svg viewBox="0 0 13 13"><path d="M3 1l2 3-1.5 1.5a7 7 0 0 0 4 4L9 8l3 2-1 2c-5 0-10-5-10-10z" fill="#bbb"/></svg></div>
<div class="input abs" style="left:99px;top:2579px;width:551px;height:105px">Message is required</div>
<div class="btn abs" style="left:99px;top:2705px;width:190px;height:40px">Send your message</div>

<p class="contact-lead abs">Sed ut perspiciatis unde omnis iste natus error sit accusantiumer doloremque laudantium, totam rem aperiam, eaque ipsa quae ab illo inventore veritatis et quasi architecto beatae vita</p>

<div class="info-label abs" style="top:2524px">Address:</div>
<div class="info-line abs" style="top:2561px"><svg viewBox="0 0 20 20"><path d="M10 19s6-6.5 6-11a6 6 0 0 0-12 0c0 4.5 6 11 6 11z" fill="none" stroke="#0b6fc2" stroke-width="1.5"/><circle cx="10" cy="8" r="2.2" fill="none" stroke="#0b6fc2" stroke-width="1.5"/></svg>Kaldera 12 10115 Tallinn ESTONIA</div>
<div class="info-label abs" style="top:2598px">Phone:</div>
<div class="info-line abs" style="top:2632px"><svg viewBox="0 0 20 20"><path d="M4 2l3 4-2 2a10 10 0 0 0 7 7l2-2 4 3-2 3C9 19 1 11 1 4z" fill="none" stroke="#0b6fc2" stroke-width="1.5"/></svg>Telephone: <span class="big">+372 55 18320</span></div>
<div class="info-label abs" style="top:2670px">Mail:</div>
<div class="info-line abs" style="top:2702px"><svg viewBox="0 0 20 20"><rect x="1" y="4" width="18" height="12" fill="none" stroke="#0b6fc2" stroke-width="1.5"/><path d="M1 4l9 7 9-7" fill="none" stroke="#0b6fc2" stroke-width="1.5"/></svg>e-mail: hello@praxelun.ee</div>

<footer class="site-footer abs">
  <span class="copy">Copyright © 2016 &nbsp;Praxelun &nbsp;&nbsp;| All rights Reserved.</span>
  <span class="follow-f">Follow With Us:</span>
  <div class="circles"><span></span><span></span><span></span><span></span></div>
</footer>

</body>
</html>
```